VELKO Website Redesign in Wix

Task:
Create a new design for all pages of the VELKO technology website in Wix. Specifications are:
Color palette preferences: black, white, gray, purple, blue. See VELKO Ref Doc provided.
Please refer to the VELKO_ref doc for a sample of the desired color palette
Typesetting must be in Montserrat
Brand will be that of a Marketing Technology company
Looking for vibrant, highly engaging images and organized, digestible flow. Open to suggestions
Required format is Wix.
VELKO logo does NOT need to be redesigned. Please use the files provided for the VELKO logo.
Look and feel
Each slider illustrates characteristics of the customer's brand and the style your logo design should communicate.

```html
<!DOCTYPE html>
<html lang="en">
<head>
<meta charset="utf-8">
<title>VELKO — Marketing Technology</title>
<link rel="stylesheet" href="https://fonts.googleapis.com/css2?family=Montserrat:wght@400;500;600;700;800&family=Lato:wght@400;700&display=swap">
<style>
:root{
  --navy:#0d2036;
  --navy-deep:#07121f;
  --blue:#0f5fa8;
  --blue-line:#3f84c4;
  --purple:#3b1456;
  --ink:#111111;
  --white:#ffffff;
  --gray:#9a9a9a;
  --rule:#d6d6d6;
  --footer:#111111;
}
*{margin:0;padding:0;box-sizing:border-box}
html,body{width:1200px;height:3960px;overflow:hidden}
body{position:relative;background:var(--white);font-family:"Lato",sans-serif;color:var(--ink)}
.abs{position:absolute}
.head{font-family:"Montserrat",sans-serif;font-weight:700;text-transform:uppercase}

/* hero */
.hero{left:0;top:0;width:1200px;height:634px;background:linear-gradient(100deg,#0a1a2c 0%,#13283f 45%,#1f3550 70%,#0e1f33 100%)}
.hero-visual{left:600px;top:0;width:600px;height:634px;background:radial-gradient(ellipse at 60% 55%,rgba(80,200,230,.35),rgba(13,32,54,0) 60%)}
.logo{font-family:"Montserrat",sans-serif;font-weight:500;letter-spacing:10px;color:var(--white)}
.hero .logo{left:112px;top:24px;font-size:38px}
.nav{left:333px;top:41px;display:flex;gap:28px;font-family:"Montserrat",sans-serif;font-size:15px;color:var(--white);text-transform:uppercase}
.hero-title{left:112px;top:248px;font-size:36px;color:var(--white);font-weight:800}
.hero-text{left:112px;top:302px;width:380px;font-size:13px;line-height:26px;color:var(--white)}
.btn-start{left:112px;top:375px;width:174px;height:51px;background:#0f5fb8;color:var(--white);font-family:"Montserrat",sans-serif;font-weight:700;font-size:15px;display:flex;align-items:center;justify-content:center;gap:10px}

/* about */
.about-title{left:124px;top:710px;font-size:40px;font-weight:800}
.about-arrow{left:124px;top:774px}
.about-claim{left:657px;top:710px;width:480px;font-family:"Lato",sans-serif;font-size:27px;line-height:38px;text-transform:uppercase}
.about-rule{left:0;top:862px;width:1200px;height:1px;background:var(--rule)}
.member{top:917px;width:269px}
.member .photo{width:269px;height:346px;background:linear-gradient(180deg,#efefef,#dcdcdc 60%,#3a3a3a 100%)}
.member .name{margin-top:24px;font-family:"Montserrat",sans-serif;font-weight:600;font-size:15px;text-transform:uppercase}
.member .role{margin-top:12px;font-size:14px}
.btn-purple{left:493px;top:1379px;width:210px;height:54px;background:var(--purple);color:var(--white);font-family:"Montserrat",sans-serif;font-size:14px;display:flex;align-items:center;justify-content:center;border-radius:3px;text-transform:uppercase}

/* blue bands */
.band{left:0;width:1200px;background:var(--blue);color:var(--white)}
.band-title{width:1200px;text-align:center;font-size:38px;line-height:40px;font-weight:800}
.grid{left:0;width:1200px;border-top:1px solid var(--blue-line);display:grid;grid-template-columns:393px 413px 394px}
.cell{height:189px;border-bottom:1px solid var(--blue-line);border-right:1px solid var(--blue-line);display:flex;align-items:center;justify-content:center;text-align:center;font-size:15px;line-height:26px;color:var(--white)}
.cell:nth-child(3n){border-right:none}
.cell-photo{background:linear-gradient(120deg,#1b2a3a,#3d5a78 50%,#6c7f93)}
.btn-outline{width:152px;height:55px;border:1px solid var(--white);border-radius:3px;color:var(--white);font-family:"Montserrat",sans-serif;font-size:14px;display:flex;align-items:center;justify-content:center;text-transform:uppercase}
.client{font-family:"Montserrat",sans-serif;font-weight:600;font-size:22px;display:flex;align-items:center;gap:10px}
.client .dot{width:22px;height:22px;border-radius:50%;background:var(--white)}

/* events */
.events-title{left:0;top:2255px;width:1200px;text-align:center;font-size:38px;font-weight:800}
.event{top:2353px;width:314px;height:330px;border:1px solid #cfcfcf}
.event .pic{height:209px}
.event .ttl{margin:24px 22px 0;padding-bottom:14px;border-bottom:1px solid var(--rule);font-family:"Montserrat",sans-serif;font-weight:700;font-size:15px;text-transform:uppercase}
.event .meta{margin:14px 22px 0;display:flex;align-items:center;font-size:14px;gap:8px}
.event .meta .heart{margin-left:auto}

/* footer */
.footer{left:0;top:3422px;width:1200px;height:538px;background:var(--footer);color:var(--white)}
.footer .logo{left:115px;top:54px;font-size:38px}
.f-label{font-family:"Montserrat",sans-serif;font-weight:700;font-size:16px;text-transform:uppercase}
.f-head{left:375px;top:108px;font-size:33px;line-height:40px;font-weight:800}
.field{font-size:14px;border-bottom:1px solid #8a8a8a;padding-bottom:16px}
.btn-submit{left:376px;top:449px;width:136px;height:50px;background:#0f5fb8;font-family:"Montserrat",sans-serif;font-weight:700;font-size:15px;display:flex;align-items:center;justify-content:center;border-radius:2px}
.f-text{font-size:14px;line-height:26px}
.social{left:876px;top:366px;display:flex;gap:10px}
.social span{width:30px;height:30px;border:1.5px solid var(--white);border-radius:50%}
</style>
</head>
<body>

<header class="abs hero">
  <div class="abs hero-visual" role="img" aria-label="Businessman holding a glowing tablet with floating marketing icons"></div>
  <div class="abs logo">VELKO</div>
  <nav class="abs nav"><span>Home</span><span>How it works</span><span>VELKO Applications</span><span>Company</span><span>More</span><span>Contact us</span></nav>
  <h1 class="abs head hero-title">Welcome to VELKO</h1>
  <p class="abs hero-text">Increase and perfect your connection with consumers using VELKO patented self-service content delivery technology.</p>
  <a class="abs btn-start">GET STARTED
    <svg width="16" height="16" viewBox="0 0 16 16"><circle cx="8" cy="8" r="8" fill="#fff"/><path d="M5 8h5M8 5l3 3-3 3" stroke="#0f5fb8" stroke-width="2" fill="none"/></svg>
  </a>
</header>

<section>
  <h2 class="abs head about-title">About us</h2>
  <svg class="abs about-arrow" width="34" height="34" viewBox="0 0 34 34"><path d="M2 2L32 32M32 10V32H10" stroke="#111" stroke-width="2" fill="none"/></svg>
  <p class="abs about-claim">We own all rights, trademarks and copyrights to VELKO™ technology globally.</p>
  <div class="abs about-rule"></div>

  <div class="abs member" style="left:120px"><div class="photo" role="img" aria-label="Portrait of Theo Marlowe"></div><div class="name">Theo Marlowe</div><div class="role">Co-Founder and Chief Technology Officer</div></div>
  <div class="abs member" style="left:465px"><div class="photo" role="img" aria-label="Portrait of Rena Okafor"></div><div class="name">Rena Okafor</div><div class="role">Co-Founder &amp; Chief Marketing Officer</div></div>
  <div class="abs member" style="left:811px"><div class="photo" role="img" aria-label="Portrait of Dale Fenwick"></div><div class="name">Dale Fenwick</div><div class="role">Chief Information Officer</div></div>
  <a class="abs btn-purple">Learn more about us</a>
</section>

<section class="abs band" style="top:1519px;height:656px">
  <h2 class="abs head band-title" style="top:42px">Strategy towards market<br>dominance</h2>
  <div class="abs grid" style="top:146px">
    <div class="cell">Digital Rights Management<br>Application</div>
    <div class="cell">AD Tech licensing</div>
    <div class="cell">Platform Integrations</div>
    <div class="cell cell-photo" role="img" aria-label="Operator working at a broadcast control desk with monitors"></div>
    <div class="cell">Technology Licensing</div>
    <div class="cell">NFT Security</div>
  </div>
  <a class="abs btn-outline" style="left:524px;top:555px">Read more</a>
</section>

<section>
  <h2 class="abs head events-title">Upcoming event</h2>
  <article class="abs event" style="left:110px"><div class="pic" role="img" aria-label="Hand holding a glowing digital network" style="background:radial-gradient(circle at 50% 50%,#8fc6ff,#1f4f9a 45%,#0a1d45)"></div><div class="ttl">Crestline Trading</div><div class="meta">👁 0 <span style="margin-left:14px">Write a comments</span><span class="heart" style="color:#e03a3a">♡</span></div></article>
  <article class="abs event" style="left:442px"><div class="pic" role="img" aria-label="Hands holding a phone with floating app icons" style="background:radial-gradient(circle at 50% 60%,#f09a4a,#2a4a7a 45%,#0d1b33)"></div><div class="ttl">Harbor Business</div><div class="meta">👁 0 <span style="margin-left:14px">Write a comments</span><span class="heart" style="color:#e03a3a">♡</span></div></article>
  <article class="abs event" style="left:774px"><div class="pic" role="img" aria-label="Hands typing on a laptop with overlay icons" style="background:linear-gradient(135deg,#b8bcc0,#6e7479 55%,#3b3f43)"></div><div class="ttl">Northgate Television</div><div class="meta">👁 0 <span style="margin-left:14px">Write a comments</span><span class="heart" style="color:#e03a3a">♡</span></div></article>
</section>

<section class="abs band" style="top:2769px;height:653px">
  <h2 class="abs head band-title" style="top:50px">Our clients</h2>
  <div class="abs grid" style="top:128px">
    <div class="cell"><span class="client"><span class="dot"></span>Brightcap Ltd</span></div>
    <div class="cell"><span class="client">Stackhold</span></div>
    <div class="cell"><span class="client" style="font-size:20px;line-height:26px;text-align:center">Gallery Week<br>Coral Bay</span></div>
    <div class="cell"><span class="client" style="font-weight:500;font-size:17px;letter-spacing:3px">LUMEN &amp; VARO</span></div>
    <div class="cell"><span class="client">Harbor Business</span></div>
    <div class="cell"><span class="client"><span class="dot" style="border-radius:3px"></span>Crestline</span></div>
  </div>
  <a class="abs btn-outline" style="left:523px;top:547px">Read more</a>
</section>

<footer class="abs footer">
  <div class="abs logo">VELKO</div>
  <div class="abs f-label" style="left:375px;top:62px">Contact us</div>
  <h2 class="abs head f-head">What can we<br>help you with?</h2>
  <div class="abs field" style="left:375px;top:229px;width:178px">First Name:</div>
  <div class="abs field" style="left:597px;top:229px;width:157px">Last Name:</div>
  <div class="abs field" style="left:375px;top:304px;width:178px">Email:</div>
  <div class="abs field" style="left:597px;top:304px;width:157px">Phone:</div>
  <div class="abs field" style="left:375px;top:379px;width:379px">Leave us a message:</div>
  <a class="abs btn-submit">SUIBMIT</a>

  <div class="abs f-label" style="left:876px;top:62px">Address</div>
  <p class="abs f-text" style="left:876px;top:98px">122, Sed ut perspiciatis unde<br>omnis natus error voluptatem.</p>
  <div class="abs f-label" style="left:876px;top:180px">Phone</div>
  <p class="abs f-text" style="left:876px;top:216px">1-866-555-0147</p>
  <div class="abs f-label" style="left:876px;top:272px">Email</div>
  <p class="abs f-text" style="left:876px;top:308px">info@velkotech.com</p>
  <div class="abs social"><span></span><span></span><span></span><span></span></div>
  <p class="abs" style="left:876px;top:440px;font-size:13px">© 2022 VELKO All Rights Reserved.</p>
  <p class="abs" style="left:1128px;top:480px;font-size:13px">C47</p>
</footer>

</body>
</html>
```